Landing page for Quorvath Computer Support

We need a high converting landing page for PPC campaign for Quorvath Computer Support. We are looking for a responsive page which works for PC, BRELVIX and Mobile devices. Main purpose of page will be to generate calls to our Toll free number. Users can also opt for chat with technician to resolve their issues but only CTA of page should be to generate call to our toll free number.
Current landing page we use is- https://brivandohelp.example/quorvath-computer-support.html (called Link1 in text below)
We will need following in new landing page:
1. Disclaimer - This is legally mandatory near CTA
PelmoraAssist is an independent provider of technical support services for several third party brands. If your product is under warranty or not repair service maybe available at brand owner or official website. Use of names, trademarks is for reference only. We disclaim any ownership, right, affiliation or endorsement of or by any such third party products or brands.
2. New Image of Customer Service Rep. See Link1
3. Description/details of what support for Quorvath we provide. See Link1. You can take some or all content from link1
4. Testimonials
5. Chat option
6. Footer with following- Contact Info and copyright statement. See Link1
7. You can place trust building logo like Zintrel Secure and Halcorix to your choice to increase effectiveness of landing page
Take ideas from http://plovique.example/landing-page-articles/the-anatomy-of-a-landing-page/. We can put whatever is necessary on new landing page to reach goal of high conversions.
Landing pages designs we like:
http://www.setup-shieldkit.example/5920147/zintrel/zintrel-support.html
http://www.mendbayo.example/quorvath/quorvath_support/quorvath_help_support.php
http://fluxdorin.example/fix-computer/
New Details:
-----------------
I generally prefer white background for landing pages. You can also use grey and any other color which goes with it. In the end, goal is high conversion rate.
Updates
Since some of the designs posted have ability to collect email address, I would like to clarify that Only CTA is to call toll free number. We don't need to collect email addresses. Reason is 99.9% of customers will only reach out to us if they have an urgent and immediate problem to resolve. They will call toll free and get support via remote connection but won't send email. Very few will opt to chat with technician. Even if they send email, they will never buy our services because they would have contacted somebody else to solve their immediate problem via remote connection.
Thanks
Home users and small business

```html
<!DOCTYPE html>
<html lang="en">
<head>
<meta charset="utf-8">
<title>Quorvath Computer Support – Brevlon Support</title>
<link rel="stylesheet" href="https://fonts.googleapis.com/css2?family=Lato:wght@300;400;700;900&family=Roboto:wght@400;500;700;900&display=swap">
<style>
:root{
  --blue:#2a87c2;
  --blue-dark:#1f6d9e;
  --blue-footer:#2c8bc5;
  --ink:#222;
  --text:#555;
  --grey:#a6a6a6;
  --grey-light:#e4e4e4;
  --gold:#f5c33b;
  --green:#3dbd5d;
  --footer-dark:#323232;
}
*{box-sizing:border-box;margin:0;padding:0}
html,body{width:1200px;height:2428px;overflow:hidden;background:#fff}
body{font-family:Lato,Arial,sans-serif;color:var(--text);position:relative}
.abs{position:absolute}
ul{list-style:none}

/* header */
.site-header{left:0;top:0;width:1200px;height:100px;border-bottom:4px solid var(--blue)}
.brand{left:138px;top:22px;display:flex;align-items:center;gap:10px}
.brand-dot{width:36px;height:36px;border-radius:50%;background:#9a9a9a}
.brand-name{font-size:34px;font-weight:700;color:#2a2a2a;letter-spacing:-.5px}
.call-box{left:766px;top:20px;display:flex;align-items:center;gap:14px}
.call-icon{width:54px;height:54px;background:var(--blue);display:flex;align-items:center;justify-content:center}
.call-label{font-size:24px;font-weight:900;color:#222;line-height:1}
.call-number{font-size:34px;font-weight:700;color:var(--blue);line-height:1.1}

/* hero */
.hero{left:0;top:104px;width:1200px;height:392px;border-bottom:4px solid var(--blue);
  background:linear-gradient(90deg,#f4f4f4 0%,#ececec 35%,#cfc4bc 60%,#c69b86 75%,#e9e2dc 100%)}
.hero-title{left:138px;top:244px;font-size:39px;font-weight:700;color:#111;line-height:1.35}
.hero-title span{color:var(--blue)}
.dots{left:578px;top:478px;display:flex;gap:4px}
.dots i{width:8px;height:8px;background:#fff;border:1px solid #bbb;display:block}
.dots i.on{background:var(--blue);border-color:var(--blue)}

/* offer */
.rule-line{top:545px;height:0;border-top:1px dashed #ccc}
.offer-title{left:0;top:526px;width:1200px;text-align:center;font-size:27px;font-weight:700;color:#666}
.offer-title span{color:var(--blue)}
.plan{top:599px;width:296px;height:170px;box-shadow:0 6px 8px -4px rgba(0,0,0,.25)}
.plan-tab{height:48px;font-size:21px;color:#555;display:flex;align-items:center;justify-content:center;
  background:linear-gradient(#f1f1f1,#d6d6d6)}
.plan-body{margin:0 6px;height:122px;background:var(--grey);color:#fff;font-size:12px;line-height:1.45;text-align:center;padding:14px 30px}
.plan.gold .plan-tab{background:linear-gradient(#fbd558,#efb526);color:#5a4410}
.plan.gold .plan-body{background:var(--blue)}

/* support */
.support-head{left:138px;top:826px;display:flex;align-items:center;gap:10px;font-size:27px;font-weight:700;color:#9a9a9a}
.head-dot{width:30px;height:30px;border-radius:50%;background:#b5b5b5}
.divider{left:724px;top:830px;height:370px;border-left:1px solid #e2e2e2}
.call-at{left:138px;top:890px;font-size:27px;font-weight:700;color:#111}
.call-at span,.ring span{color:var(--blue)}
.copy{font-size:13px;line-height:1.55;color:#444}
.ticks li{display:flex;align-items:center;gap:10px;font-size:14px;font-weight:700;color:#333;height:28.5px}
.tick{width:14px;height:14px;flex:none}
.side-title{left:755px;top:832px;width:320px;font-size:18px;font-weight:700;color:var(--blue);line-height:1.4}
.side-list{left:755px;top:918px;width:320px}
.side-list li{display:flex;gap:14px;font-size:13px;font-weight:700;color:#333;line-height:1.5;margin-bottom:18px}
.side-list .tick{margin-top:3px}

/* ring */
.ring{left:138px;top:1222px;font-size:27px;font-weight:700;color:#111;line-height:1.3}
.box247{left:755px;top:1228px;width:308px;height:154px;background:var(--blue);color:#fff;text-align:center;font-family:Roboto,Arial,sans-serif}
.box247 b{display:block;font-size:50px;font-weight:700;margin-top:6px;line-height:1.1}
.box247 span{display:block;font-size:29px;line-height:1.2}
.diag{left:762px;top:1402px;font-size:19px;font-weight:900;color:#222;line-height:1.35;font-family:Roboto,Arial,sans-serif;white-space:nowrap}
.chat{left:755px;top:1461px;width:203px;height:54px;background:var(--green);color:#fff;font-size:34px;font-weight:700;
  font-family:Roboto,Arial,sans-serif;display:flex;align-items:center;justify-content:center}
.agent{left:985px;top:1426px;width:78px;height:90px;border-radius:40px 40px 0 0;background:linear-gradient(#c99a82,#7a4f3c)}
.fade-rule{left:180px;top:1562px;width:840px;height:6px;background:radial-gradient(ellipse at center,rgba(0,0,0,.18),rgba(0,0,0,0) 70%)}

/* testimonials */
.testi{top:1613px;width:310px}
.avatar{width:80px;height:80px;border-radius:50%;border:3px solid #cfe0ec}
.t-name{position:absolute;left:100px;top:10px;font-size:21px;color:#555}
.t-role{position:absolute;left:110px;top:42px;font-size:12px;color:#888}
.t-line{position:absolute;left:96px;top:60px;width:200px;border-top:1px solid #ddd}
.t-quote{position:absolute;left:0;top:100px;width:300px;font-size:12.5px;line-height:1.5;color:#555;padding-left:26px}
.t-quote:before{content:"\201C";position:absolute;left:2px;top:-8px;font-size:30px;color:#666;font-family:Georgia,serif}
.read-more{position:absolute;top:152px;width:140px;height:34px;background:var(--blue);color:#fff;font-size:12px;font-weight:700;
  display:flex;align-items:center;justify-content:center}

/* footer */
.footer-links{left:0;top:1838px;width:1200px;height:346px;background:var(--footer-dark)}
.fl-title{left:138px;top:1852px;font-size:22px;font-weight:700;color:#fff}
.fl-col{top:1896px;font-size:12.5px;color:#ddd}
.fl-col li{height:22.6px}
.footer-info{left:0;top:2184px;width:1200px;height:212px;background:var(--blue-footer)}
.fi-title{top:2200px;font-size:21px;font-weight:700;color:#fff}
.fi-list{font-size:12.5px;color:#fff}
.fi-list li{height:22.5px}
.contact{color:#fff}
.contact li{display:flex;gap:14px;align-items:flex-start;font-size:12.5px;margin-bottom:14px;line-height:1.4}
.badge{position:absolute;border-radius:3px}
.copyright{left:0;top:2396px;width:1200px;height:32px;background:var(--blue-dark);color:#fff;font-size:12.5px;
  display:flex;align-items:center;justify-content:center;letter-spacing:.3px}
</style>
</head>
<body>

<svg width="0" height="0" style="position:absolute">
  <defs>
    <symbol id="tick" viewBox="0 0 14 14">
      <rect x="0.5" y="0.5" width="13" height="13" fill="#fff" stroke="#2a87c2"/>
      <path d="M3 7.2l2.6 2.6L11 4.2" fill="none" stroke="#2a87c2" stroke-width="2"/>
    </symbol>
  </defs>
</svg>

<header class="site-header abs">
  <div class="brand abs"><span class="brand-dot"></span><span class="brand-name">Brevlon Support</span></div>
  <div class="call-box abs">
    <div class="call-icon">
      <svg width="28" height="28" viewBox="0 0 24 24"><path fill="#fff" d="M6.6 10.8a15.1 15.1 0 006.6 6.6l2.2-2.2c.3-.3.7-.4 1-.2 1.1.4 2.3.6 3.6.6.6 0 1 .4 1 1V20c0 .6-.4 1-1 1A17 17 0 013 4c0-.6.4-1 1-1h3.5c.6 0 1 .4 1 1 0 1.3.2 2.5.6 3.6.1.3 0 .7-.2 1z"/></svg>
    </div>
    <div>
      <div class="call-label">CALL US TOLL FREE</div>
      <div class="call-number">1-800-555-0142</div>
    </div>
  </div>
</header>

<section class="hero abs" role="img" aria-label="Smiling customer service representative wearing a headset"></section>
<h1 class="hero-title abs">Lorem Ipsum is<br><span>simply dummy</span> sit dolor</h1>
<div class="dots abs"><i></i><i></i><i class="on"></i><i></i></div>

<div class="rule-line abs" style="left:138px;width:330px"></div>
<div class="rule-line abs" style="left:732px;width:330px"></div>
<h2 class="offer-title abs">WHAT <span>WE OFFER</span></h2>

<div class="plan abs" style="left:138px">
  <div class="plan-tab">SILVER PLAN</div>
  <div class="plan-body">Lorem Ipsum has been the industry's standard dummy text ever since the 1500s, when an unknown printer took a galley of type and scrambled it to make a type specimen book. It has survived not only five.</div>
</div>
<div class="plan gold abs" style="left:451px">
  <div class="plan-tab">GOLD PLAN</div>
  <div class="plan-body">Lorem Ipsum has been the industry's standard dummy text ever since the 1500s, when an unknown printer took a galley of type and scrambled it to make a type specimen book. It has survived not only five.</div>
</div>
<div class="plan abs" style="left:767px">
  <div class="plan-tab">PLATINUM PLAN</div>
  <div class="plan-body">Lorem Ipsum has been the industry's standard dummy text ever since the 1500s, when an unknown printer took a galley of type and scrambled it to make a type specimen book. It has survived not only five.</div>
</div>

<h2 class="support-head abs"><span class="head-dot"></span>SUPPORT FOR QUORVATH COMPUTER</h2>
<div class="divider abs"></div>
<h3 class="call-at abs">Call at <span>1-800-555-0142</span> for instant support.</h3>
<p class="copy abs" style="left:138px;top:932px;width:560px">When you face a computer problem, identifying the problem and properly fixing it consumes precious time, labor, and resources. We are here to streamline the tech support process, offering high-quality, professional tech support for Quorvath computers. All of our technicians are fully certified and trained, with experience and expertise dealing specifically with Quorvath computers. Our technicians can efficiently deal with a range of problems and issues, including:</p>
<ul class="ticks abs" style="left:138px;top:1038px">
  <li><svg class="tick"><use href="#tick"/></svg>Diagnosis and repair of software issues</li>
  <li><svg class="tick"><use href="#tick"/></svg>Troubleshooting software errors</li>
  <li><svg class="tick"><use href="#tick"/></svg>Configuration services</li>
  <li><svg class="tick"><use href="#tick"/></svg>Security program installation</li>
  <li><svg class="tick"><use href="#tick"/></svg>Routine security maintenance</li>
</ul>

<h3 class="side-title abs">We provide Quorvath support for a variety of Quorvath products, including:</h3>
<ul class="side-list abs">
  <li><svg class="tick"><use href="#tick"/></svg><span>Quorvath G Series, Quorvath 3000 V, Quorvath 3000 C, Quorvath 3000 N</span></li>
  <li><svg class="tick"><use href="#tick"/></svg><span>Quorvath 3000 Y , Quorvath S Series, Quorvath SL Series, Quorvath R Series</span></li>
  <li><svg class="tick"><use href="#tick"/></svg><span>Quorvath T Series, Quorvath X Series, Quorvath X Series Tablet, Quorvath W Series and more...</span></li>
</ul>
<p class="copy abs" style="left:755px;top:1112px;width:320px;font-size:12.5px">All service is done remotely in order to facilitate the fastest possible service and eliminate delays that cost your organization time and money. For fast and efficient Quorvath tech support, don't hesitate to contact us.</p>

<h3 class="ring abs">Just Give Us Ring At <span>1-800-555-0142</span> For<br>Great Tech Support.</h3>
<p class="copy abs" style="left:138px;top:1302px;width:560px">Platinum Plan - Brevlon Support has "Platinum Plan" service for its honoured customers. Plan offers following features:</p>
<ul class="ticks abs" style="left:138px;top:1346px">
  <li><svg class="tick"><use href="#tick"/></svg>We offer unlimited technical support</li>
  <li><svg class="tick"><use href="#tick"/></svg>Support for antivirus, PC Clean-up and Optimization</li>
  <li><svg class="tick"><use href="#tick"/></svg>We provide complete service for updating software and drivers</li>
  <li><svg class="tick"><use href="#tick"/></svg>Support for CD/DVD burning, ZIP, Video players, Camera, MP3 players</li>
  <li><svg class="tick"><use href="#tick"/></svg>Support for printers, scanners, WIFI and Networking setup</li>
  <li><svg class="tick"><use href="#tick"/></svg>We ensure you that you will get fast resolutions</li>
</ul>

<div class="box247 abs"><b>24 x 7</b><span>Technical Support</span><span>for Quorvath Service</span></div>
<p class="diag abs">FREE Issue Diagnosis by<br>Expert Certified Techs</p>
<div class="chat abs">LIVE CHAT</div>
<div class="agent abs" role="img" aria-label="Chat support agent wearing a headset"></div>
<div class="fade-rule abs"></div>

<div class="testi abs" style="left:138px">
  <div class="avatar" role="img" aria-label="Customer portrait" style="background:radial-gradient(circle at 50% 40%,#e2b8a0,#7a4a36)"></div>
  <div class="t-name">Perspiciatis</div><div class="t-role">Lorem Ipsum</div><div class="t-line"></div>
  <p class="t-quote">Lorem Ipsum is simply dummy text of the printing and typesetting industry.</p>
  <div class="read-more" style="left:64px">READ MORE</div>
</div>
<div class="testi abs" style="left:451px">
  <div class="avatar" role="img" aria-label="Customer portrait" style="background:radial-gradient(circle at 50% 40%,#c99a82,#2e2622)"></div>
  <div class="t-name">Voluptate</div><div class="t-role">Lorem Ipsum</div><div class="t-line"></div>
  <p class="t-quote">Lorem Ipsum is simply dummy text of the printing and typesetting industry.</p>
  <div class="read-more" style="left:66px">READ MORE</div>
</div>
<div class="testi abs" style="left:795px">
  <div class="avatar" role="img" aria-label="Customer portrait" style="background:radial-gradient(circle at 50% 40%,#f0c7a8,#b9773f)"></div>
  <div class="t-name">Architecto</div><div class="t-role">Lorem Ipsum</div><div class="t-line"></div>
  <p class="t-quote">Lorem Ipsum is simply dummy text of the printing and typesetting industry.</p>
  <div class="read-more" style="left:64px">READ MORE</div>
</div>

<footer>
  <div class="footer-links abs"></div>
  <h4 class="fl-title abs">SUPPORT</h4>
  <ul class="fl-col abs" style="left:138px">
    <li>&gt; Support for Slow PC</li><li>&gt; Support for Computer Issues</li><li>&gt; Support for PC Optimization</li>
    <li>&gt; Support for PC Tuneup</li><li>&gt; Support for Brelvix</li><li>&gt; Support for Quendra</li>
    <li>&gt; Support for Fluxen</li><li>&gt; Support for Registry</li><li>&gt; Support for Tarnvue</li>
    <li>&gt; Support for Olvinu</li><li>&gt; Support for Savrelo</li>
  </ul>
  <ul class="fl-col abs" style="left:360px">
    <li>&gt; Support for Dornex Computer</li><li>&gt; Support for Hevra Computer</li><li>&gt; Support Tokaveli Computer</li>
    <li>&gt; Support For Acrona Computer</li><li>&gt; Support For Quorvath Computer</li><li>&gt; Support For Sonvera Computer</li>
    <li>&gt; Support For Comparo Computer</li><li>&gt; Support for Linvore Router</li><li>&gt; Support for Belmira Router</li>
    <li>&gt; Support for Ciskel Router</li><li>&gt; Support for Dalvane Router</li>
  </ul>
  <ul class="fl-col abs" style="left:599px">
    <li>&gt; Support for Azurik Router</li><li>&gt; Support for Zintrel Antivirus</li><li>&gt; Support for Kavetor Antivirus</li>
    <li>&gt; Support for Avelno Antivirus</li><li>&gt; Support for Agrevo Antivirus</li><li>&gt; Support for Avandri Antivirus</li>
    <li>&gt; Support for Nortavel AntiVirus</li><li>&gt; Support for Bitrovan Antivirus</li><li>&gt; Support for Dornex Printer</li>
    <li>&gt; Support for Hevra Printer</li><li>&gt; Support for Brovanti Printer</li>
  </ul>
  <ul class="fl-col abs" style="left:850px">
    <li>&gt; Support for Panvira Printer</li><li>&gt; Support for Epraxa Printer</li><li>&gt; Support for Canvello Printer</li>
    <li>&gt; Support for Samvora Printer</li><li>&gt; Support for Netrova Router</li><li>&gt; Support for Pogvane Games</li>
    <li>&gt; Support for Webrel Antivirus</li><li>&gt; Support for Vipsen Antivirus</li><li>&gt; Support for Trelmi Antivirus</li>
    <li>&gt; Support for Totrava Antivirus</li><li>&gt; Support for Pandrel Antivirus</li><li>&gt; Support for Printers</li>
  </ul>

  <div class="footer-info abs"></div>
  <h4 class="fi-title abs" style="left:138px">QUICK LINKS</h4>
  <ul class="fi-list abs" style="left:138px;top:2238px">
    <li>&gt; About Us</li><li>&gt; Contact Us</li><li>&gt; Terms &amp; Conditions</li>
    <li>&gt; Privacy Policy</li><li>&gt; Refund Policy</li><li>&gt; Disclaimer</li>
  </ul>
  <h4 class="fi-title abs" style="left:371px">CONTACT INFO</h4>
  <ul class="contact abs" style="left:371px;top:2240px;width:250px">
    <li><svg width="16" height="20" viewBox="0 0 16 20"><path fill="#fff" d="M8 0a7 7 0 00-7 7c0 5 7 13 7 13s7-8 7-13a7 7 0 00-7-7zm0 10a3 3 0 110-6 3 3 0 010 6z"/></svg><span>18 Amberlane St, Corvel Falls, NY<br>10000, USA.</span></li>
    <li><svg width="16" height="16" viewBox="0 0 24 24"><circle cx="12" cy="12" r="11" fill="none" stroke="#fff" stroke-width="2"/><path fill="#fff" d="M8.5 10.8a8 8 0 004.7 4.7l1.4-1.4c.2-.2.5-.2.7-.1l2 .8v2.6c0 .4-.3.6-.6.6A11 11 0 016 6.6c0-.3.2-.6.6-.6h2.6l.8 2c.1.2 0 .5-.1.7z"/></svg><span>1-800-555-0142</span></li>
    <li><svg width="16" height="16" viewBox="0 0 24 24"><path fill="#fff" d="M2 4h20v16H2zm2 2v1l8 5 8-5V6zm0 3.4V18h16V9.4l-8 5z"/></svg><span>212-555-0187</span></li>
    <li><svg width="16" height="14" viewBox="0 0 24 20"><path fill="#fff" d="M1 2h22v16H1zm2 2v.8l9 5.6 9-5.6V4z"/></svg><span>support@brevlonsupport.example</span></li>
  </ul>
  <h4 class="fi-title abs" style="left:672px">PLANS</h4>
  <ul class="fi-list abs" style="left:672px;top:2238px">
    <li>&gt; Silver Plan</li><li>&gt; Gold Plan</li><li>&gt; Platinum Plan</li>
  </ul>
  <div class="badge" style="left:918px;top:2206px;width:90px;height:44px;background:#fff"></div>
  <div class="badge" style="left:928px;top:2256px;width:70px;height:28px;background:#e9eef5"></div>
  <div class="badge" style="left:906px;top:2292px;width:112px;height:38px;background:#f4f7ea"></div>
  <div class="badge" style="left:862px;top:2338px;width:40px;height:22px;background:#fff"></div>
  <div class="badge" style="left:906px;top:2338px;width:40px;height:22px;background:#fff"></div>
  <div class="badge" style="left:950px;top:2338px;width:40px;height:22px;background:#fff"></div>
  <div class="badge" style="left:994px;top:2338px;width:40px;height:22px;background:#fff"></div>
  <div class="badge" style="left:1038px;top:2338px;width:28px;height:22px;background:#fff"></div>

  <div class="copyright abs">© 2014 BREVLON SUPPORT &nbsp;&nbsp;|&nbsp;&nbsp; All Rights Reserved</div>
</footer>

</body>
</html>
```